FinTech company looking to revamp and expand client-facing interface for our financial models

Pellworth Engines currently has a very simple website that allows clients to interact with our financial models. We are looking to completely redesign the current site and add several extra pages to provide extra functionality. We want the design to have a modern, slick feel, that will work on both a desktop or a tablet. It should be straightforward for clients to move between different pages at any time, and clear from the layout how to interact with the more advanced features. We have included screenshots of existing pages in the attached design brief, as well as sketches of the functionality required by the new pages, but can't provide a direct link to the current site.
Target Market(s)
Professional investors that will be paying to access the interface
Industry/Entity Type
Finance
Number of Pages Required
4 page
Colors
Designer to choose colors to be used in the design.
Look and feel
Each slider illustrates characteristics of the customer's brand and the style your logo design should communicate.

```html
<!DOCTYPE html>
<html lang="en">
<head>
<meta charset="utf-8">
<title>Pellworth Engines – Backtest</title>
<link href="https://fonts.googleapis.com/css2?family=Roboto:wght@400;500;700&family=Roboto+Condensed:wght@400;500&display=swap" rel="stylesheet">
<style>
:root{
  --navy:#0b3165;
  --teal:#0f6b63;
  --overlay:#333333;
  --dark:#1c1c1c;
  --ink:#111;
  --muted:#6b6b6b;
  --line:#e3e3e3;
  --page:#eeeeee;
  --row-alt:#f0f0f0;
  --white:#fff;
}
*{box-sizing:border-box;margin:0;padding:0}
html,body{width:1200px;height:1122px;overflow:hidden;background:var(--white)}
body{font-family:'Roboto',sans-serif;color:var(--ink)}
.stage{position:absolute;left:0;top:0;width:1300px;height:1215px;transform:scale(.9231);transform-origin:0 0}
.abs{position:absolute}
.page{left:15px;top:15px;width:1270px;height:1185px;background:var(--page)}
.topbar{left:15px;top:15px;width:1270px;height:60px;background:var(--white);box-shadow:0 2px 6px rgba(0,0,0,.08)}
.nav-cell{position:absolute;top:0;height:60px;display:flex;align-items:center;justify-content:center;gap:8px;font-weight:700;font-size:14px;border-right:1px solid var(--line)}
.brand{font-size:19px;letter-spacing:.5px}
.nav-active{background:var(--navy);color:var(--white);border:none}
.card{left:105px;top:115px;width:1160px;height:425px;background:var(--white);box-shadow:0 1px 6px rgba(0,0,0,.12)}
.card-band{left:0;top:0;width:100%;height:85px;background:#efefef}
.axis-label{font-size:12px;color:#666}
.options-tab{left:815px;top:348px;width:50px;height:249px;background:#3a3a3a;border-radius:0 6px 6px 0}
.options-tab span{position:absolute;left:9px;top:170px;transform:rotate(-90deg);transform-origin:0 0;color:var(--white);font-size:17px;letter-spacing:1.5px;font-weight:500}
.export{left:1174px;top:592px;color:var(--navy);font-weight:700;font-size:17px;display:flex;gap:8px;align-items:center}
.table{background:var(--white);box-shadow:0 1px 6px rgba(0,0,0,.12);font-family:'Roboto Condensed',sans-serif;font-size:17px}
.trow{position:absolute;left:0;height:70px;display:flex;align-items:center}
.trow.alt{background:var(--row-alt)}
.cell{text-align:center;height:100%;display:flex;align-items:center;justify-content:center;border-right:1px solid var(--line)}
.thead{background:var(--dark);color:var(--white);font-family:'Roboto',sans-serif;font-weight:500}
.thead .cell{border-right:1px solid #444}
.scroll-track{background:#d6d6d6}
.scroll-rail{position:absolute;background:var(--white);border:1px solid #bbb;border-radius:10px}
.scroll-thumb{position:absolute;background:#999;border-radius:10px}
.overlay{left:15px;top:155px;width:800px;height:635px;background:var(--overlay)}
.ghost-tab{background:#242424;color:#3c3c3c;font-size:13px;display:flex;align-items:center;justify-content:center;border-radius:4px 4px 0 0}
.mode-tab{height:46px;width:180px;border:2px solid var(--white);border-bottom:none;border-radius:6px 6px 0 0;color:var(--white);font-size:17px;font-weight:500;display:flex;align-items:center;justify-content:center}
.mode-tab.on{background:var(--navy)}
.panel{background:var(--white);border-radius:3px;overflow:hidden}
.field{border:1px solid #bbb;border-radius:3px;height:30px;padding:0 12px;font-size:15px;display:flex;align-items:center;box-shadow:inset 0 1px 2px rgba(0,0,0,.1)}
.btn{display:flex;align-items:center;justify-content:center;color:var(--white);font-weight:700;border-radius:3px}
.model-row{position:absolute;left:0;width:330px;height:50px;border-bottom:1px solid var(--line);font-weight:700;font-size:17px;padding-left:21px;display:flex;align-items:center}
.model-row.sel{background:var(--teal);color:var(--white)}
.params-head{height:50px;background:#6b6b6b;color:var(--white);font-weight:700;font-size:18px;display:flex;align-items:center;justify-content:center}
.param-row{position:absolute;left:0;width:370px;height:50px;border-bottom:1px solid var(--line);display:flex;align-items:center}
.param-row b{width:114px;padding-left:18px;font-size:17px}
.param-row .field{width:241px}
</style>
</head>
<body>
<div class="stage">
  <div class="abs page"></div>

  <header class="abs topbar">
    <div class="nav-cell brand" style="left:0;width:180px">PELLWORTH</div>
    <div class="nav-cell" style="left:180px;width:90px">250D</div>
    <div class="nav-cell" style="left:270px;width:90px">83D</div>
    <div class="nav-cell" style="left:360px;width:90px">42D</div>
    <div class="nav-cell" style="left:450px;width:136px"></div>
    <div class="nav-cell" style="left:586px;width:140px;border-left:1px solid var(--line)">
      <svg width="24" height="22" viewBox="0 0 24 22"><path d="M2 11 12 2l10 9M5 9v11h5v-6h4v6h5V9" fill="none" stroke="#111" stroke-width="2.4"/></svg>MODELS</div>
    <div class="nav-cell" style="left:726px;width:178px">
      <svg width="24" height="24" viewBox="0 0 24 24"><g fill="#111"><circle cx="12" cy="12" r="3"/><circle cx="12" cy="3" r="2"/><circle cx="12" cy="21" r="2"/><circle cx="3" cy="12" r="2"/><circle cx="21" cy="12" r="2"/><circle cx="5.5" cy="5.5" r="2"/><circle cx="18.5" cy="18.5" r="2"/><circle cx="18.5" cy="5.5" r="2"/><circle cx="5.5" cy="18.5" r="2"/></g></svg>SENSITIVITIES</div>
    <div class="nav-cell" style="left:904px;width:160px">
      <svg width="24" height="24" viewBox="0 0 24 24"><g fill="none" stroke="#111" stroke-width="2"><circle cx="6" cy="6" r="4"/><circle cx="18" cy="6" r="4"/><circle cx="6" cy="18" r="4"/><circle cx="18" cy="18" r="4"/></g></svg>PORTFOLIO</div>
    <div class="nav-cell nav-active" style="left:1064px;width:151px">
      <svg width="26" height="20" viewBox="0 0 26 20"><rect x="1" y="1" width="24" height="18" fill="none" stroke="#fff" stroke-width="2"/><path d="M5 14l5-5 4 3 6-6" fill="none" stroke="#fff" stroke-width="2"/></svg>BACKTEST</div>
  </header>

  <section class="abs card">
    <div class="abs card-band"></div>
    <svg class="abs" style="left:690px;top:130px" width="420" height="240" viewBox="0 0 420 240">
      <g stroke="#e5e5e5"><line x1="0" y1="18" x2="315" y2="18"/><line x1="0" y1="55" x2="315" y2="55"/><line x1="0" y1="100" x2="315" y2="100"/><line x1="0" y1="150" x2="315" y2="150"/></g>
      <line x1="0" y1="205" x2="315" y2="205" stroke="#888"/>
      <line x1="0" y1="20" x2="270" y2="21" stroke="#c8c02c" stroke-width="6" stroke-dasharray="8 3"/>
      <line x1="0" y1="17" x2="270" y2="17" stroke="#3f73b8" stroke-width="6" stroke-dasharray="9 2"/>
      <circle cx="241" cy="201" r="3.5" fill="#4a9a2e"/><circle cx="248" cy="201" r="3.5" fill="#4a9a2e"/>
    </svg>
    <div class="abs axis-label" style="left:786px;top:349px">May 2019</div>
    <div class="abs axis-label" style="left:930px;top:349px">Jul 2019</div>
    <div class="abs" style="left:1062px;top:139px;font-size:12px;color:#444;font-family:serif">Names</div>
    <svg class="abs" style="left:1040px;top:142px" width="10" height="196">
      <g><circle cx="5" cy="5" r="3.5" fill="#8ab4dd"/><circle cx="5" cy="23" r="3.5" fill="#f0a86a"/><circle cx="5" cy="42" r="3.5" fill="#3f9a3f"/><circle cx="5" cy="60" r="3.5" fill="#e87c8a"/><circle cx="5" cy="79" r="3.5" fill="#c6a6da"/><circle cx="5" cy="97" r="3.5" fill="#c7a39a"/><circle cx="5" cy="116" r="3.5" fill="#f1b6d8"/><circle cx="5" cy="134" r="3.5" fill="#bbbbbb"/><circle cx="5" cy="153" r="3.5" fill="#c7c43a"/><circle cx="5" cy="171" r="3.5" fill="#8fd6e6"/><circle cx="5" cy="190" r="3.5" fill="#2f5d9f"/></g>
    </svg>
  </section>

  <div class="abs options-tab"><span>OPTIONS</span></div>
  <svg class="abs" style="left:850px;top:457px" width="30" height="30" viewBox="0 0 30 30"><circle cx="15" cy="15" r="13" fill="var(--navy)" stroke="#fff" stroke-width="2"/><path d="M21 15H9m5-5-5 5 5 5" fill="none" stroke="#fff" stroke-width="2.2"/></svg>

  <div class="abs export"><svg width="26" height="22" viewBox="0 0 26 22"><path d="M14 3H3v17h18v-7M12 13l11-10m-6 0h6v6" fill="none" stroke="var(--navy)" stroke-width="2.2"/></svg>Export</div>

  <!-- stats table -->
  <div class="abs table" style="left:105px;top:700px;width:400px;height:420px">
    <div class="trow" style="top:0;width:360px"><div class="cell" style="width:180px"></div><div class="cell" style="width:180px"></div></div>
    <div class="trow alt" style="top:70px;width:360px"><div class="cell" style="width:180px">Stat 2</div><div class="cell" style="width:180px">-3</div></div>
    <div class="trow" style="top:140px;width:360px"><div class="cell" style="width:180px">Stat 3</div><div class="cell" style="width:180px">30%</div></div>
    <div class="trow alt" style="top:210px;width:360px"><div class="cell" style="width:180px">Stat 4</div><div class="cell" style="width:180px">0.5</div></div>
    <div class="trow" style="top:280px;width:360px"><div class="cell" style="width:180px">Stat 5</div><div class="cell" style="width:180px">-3</div></div>
    <div class="trow alt" style="top:350px;width:360px"><div class="cell" style="width:180px">Stat 6</div><div class="cell" style="width:180px">30%</div></div>
    <div class="abs scroll-track" style="left:360px;top:0;width:40px;height:420px"><div class="scroll-rail" style="left:11px;top:40px;width:18px;height:355px"></div></div>
  </div>

  <!-- trades table -->
  <div class="abs table" style="left:545px;top:630px;width:720px;height:490px">
    <div class="trow thead" style="top:0;width:720px"><div class="cell" style="width:180px"></div><div class="cell" style="width:180px">Close</div><div class="cell" style="width:180px">Size</div><div class="cell" style="width:180px;border:none">Return</div></div>
    <div class="trow" style="top:70px;width:680px"><div class="cell" style="width:180px"></div><div class="cell" style="width:180px">2018-04-07</div><div class="cell" style="width:180px">13</div><div class="cell" style="width:140px">5%</div></div>
    <div class="trow alt" style="top:140px;width:680px"><div class="cell" style="width:180px">2018-04-05</div><div class="cell" style="width:180px">2018-04-07</div><div class="cell" style="width:180px">12</div><div class="cell" style="width:140px">7%</div></div>
    <div class="trow" style="top:210px;width:680px"><div class="cell" style="width:180px">2018-04-05</div><div class="cell" style="width:180px">2018-04-07</div><div class="cell" style="width:180px">15</div><div class="cell" style="width:140px">6%</div></div>
    <div class="trow alt" style="top:280px;width:680px"><div class="cell" style="width:180px">2018-04-05</div><div class="cell" style="width:180px">2018-04-07</div><div class="cell" style="width:180px">16</div><div class="cell" style="width:140px">9%</div></div>
    <div class="trow" style="top:350px;width:680px"><div class="cell" style="width:180px">2018-04-05</div><div class="cell" style="width:180px">2018-04-07</div><div class="cell" style="width:180px">12</div><div class="cell" style="width:140px">8%</div></div>
    <div class="trow alt" style="top:420px;width:680px"><div class="cell" style="width:180px">2018-04-05</div><div class="cell" style="width:180px">2018-04-07</div><div class="cell" style="width:180px">19</div><div class="cell" style="width:140px">6%</div></div>
    <div class="abs scroll-track" style="left:680px;top:70px;width:40px;height:420px"><div class="scroll-rail" style="left:11px;top:25px;width:18px;height:370px"></div><div class="scroll-thumb" style="left:11px;top:25px;width:18px;height:75px"></div></div>
  </div>

  <!-- model options overlay -->
  <div class="abs overlay"></div>
  <div class="abs ghost-tab" style="left:160px;top:165px;width:155px;height:35px">C</div>
  <div class="abs ghost-tab" style="left:605px;top:155px;width:90px;height:45px">#4</div>
  <div class="abs mode-tab on" style="left:230px;top:175px">Mode 1</div>
  <div class="abs mode-tab" style="left:420px;top:175px">Mode 2</div>

  <div class="abs panel" style="left:35px;top:240px;width:370px;height:530px">
    <div class="abs field" style="left:17px;top:10px;width:180px">Model name</div>
    <div class="abs btn" style="left:208px;top:10px;width:104px;height:30px;background:var(--teal);font-size:16px">Select</div>
    <div class="abs" style="left:0;top:50px;width:330px;border-top:1px solid var(--line)"></div>
    <div class="model-row" style="top:51px">Model 1</div>
    <div class="model-row" style="top:101px">Model 2</div>
    <div class="model-row sel" style="top:151px">Model 3</div>
    <div class="model-row" style="top:200px">Model 4</div>
    <div class="model-row" style="top:250px">Model 5</div>
    <div class="model-row" style="top:300px">Model 6</div>
    <div class="model-row" style="top:350px">Model 7</div>
    <div class="model-row" style="top:400px">Model 8</div>
    <div class="abs scroll-track" style="left:330px;top:50px;width:40px;height:400px"><div class="scroll-rail" style="left:10px;top:25px;width:19px;height:350px"></div><div class="scroll-thumb" style="left:10px;top:25px;width:19px;height:75px"></div></div>
    <div class="abs btn" style="left:87px;top:470px;width:195px;height:40px;background:var(--navy);font-size:14px;gap:12px">
      <svg width="22" height="22" viewBox="0 0 22 22"><circle cx="11" cy="11" r="9.5" fill="none" stroke="#fff" stroke-width="1.6"/><path d="M11 6v10M6 11h10" stroke="#fff" stroke-width="1.6"/></svg>ADD A MODEL</div>
  </div>

  <div class="abs panel" style="left:425px;top:240px;width:370px;height:530px">
    <div class="params-head">Parameters:</div>
    <div class="param-row" style="top:50px"><b>Entry:</b><div class="field">0.5</div></div>
    <div class="param-row" style="top:100px"><b>Exit:</b><div class="field">-0.3</div></div>
    <div class="param-row" style="top:150px"><b>Lookback:</b><div class="field">5</div></div>
    <div class="param-row" style="top:200px"><b>Entry:</b><div class="field">0.5</div></div>
    <div class="param-row" style="top:250px"><b>Exit:</b><div class="field">-0.3</div></div>
    <div class="param-row" style="top:300px"><b>Lookback:</b><div class="field">5</div></div>
    <div class="param-row" style="top:350px"><b>Entry:</b><div class="field">0.5</div></div>
    <div class="param-row" style="top:400px"><b>Exit:</b><div class="field">-0.3</div></div>
    <div class="abs btn" style="left:109px;top:466px;width:153px;height:48px;background:var(--navy);font-size:16px">RUN</div>
  </div>
</div>
</body>
</html>
```